Podiatry clinic requires a modern revamp and editing of existing website.

I would like a fresh new look and updated information for my current business website. An easy to navigate site with prominent address and phone number for call to action. We are a podiatry clinic that focuses on general and sports podiatry.
I would like 4 pages; including Home page, About Us, Services & Contact.
www.brambleridgepodiatry.net

Target Market(s)

Active working professionals.

Industry/Entity Type

Medical

Coding

Coded - Design and coding required

Number of Pages Required

4 page

Font styles to use
Sans Serif

Colors
6b449b

Requirements
Must have
• A modern look with logo and active images; clean and uncluttered. Visible phone number and address for call to action.
• 4 pages - Home, About Us, Services, Contact.
• Home page - update address & service logos.
• About Us - update of personal information.
• Services - Revamp of existing page.
• Contact page to include Google map, email & phone number.
Nice to have
• Ability to add content easily; eg. a blog or adding video onto Home page.
• Link to Facebook page.

```html
<!DOCTYPE html>
<html lang="en">
<head>
<meta charset="utf-8">
<title>Bramble Ridge Podiatry</title>
<link href="https://fonts.googleapis.com/css2?family=Cabin:wght@500;600;700&family=Open+Sans:wght@400;600;700&display=swap" rel="stylesheet">
<style>
:root{
  --purple:#6b449b;
  --purple-deep:#4a2d8f;
  --purple-dark:#3f2574;
  --purple-light:#9b82cb;
  --logo-box:#8a70bd;
  --frame:#dcdcdc;
  --ink:#2b2b2b;
  --body:#3a3a3a;
  --nav:#161616;
  --footer:#1d1d1d;
  --welcome-bg:#f2f6f9;
  --white:#ffffff;
}
*{box-sizing:border-box;margin:0;padding:0}
html,body{width:695px;height:1200px;overflow:hidden;background:var(--frame)}
body{font-family:"Open Sans",Arial,sans-serif;color:var(--body)}
.page{position:relative;width:695px;height:1200px}
.abs{position:absolute}

/* header */
.site-header{left:8px;top:8px;width:679px;height:70px;background:linear-gradient(180deg,#5d3d8c,#6f4ea0)}
.top-strip{left:436px;top:8px;width:242px;height:22px;background:#8069b0;clip-path:polygon(0 0,100% 0,90% 100%,8% 100%);display:flex;align-items:center;justify-content:center;gap:8px;color:var(--white);font-size:8px;font-weight:600}
.social-dot{display:inline-block;width:10px;height:10px;border:1px solid var(--white);border-radius:50%}
.logo-box{left:44px;top:8px;width:122px;height:82px;background:var(--logo-box);box-shadow:0 2px 4px rgba(0,0,0,.3);display:flex;align-items:center;justify-content:center;gap:6px;padding:0 8px}
.logo-dot{width:12px;height:12px;border-radius:50%;background:var(--white);flex:none}
.logo-name{font-family:"Cabin",sans-serif;font-weight:700;font-size:14px;line-height:1.1;color:var(--white)}
.contact-row{left:326px;top:47px;width:350px;display:flex;justify-content:flex-end;gap:18px;color:var(--white);font-family:"Cabin",sans-serif;font-weight:600;font-size:10.5px;align-items:center}
.contact-row span{display:flex;align-items:center;gap:5px}
.main-nav{left:8px;top:78px;width:679px;height:26px;background:var(--nav)}
.main-nav a{position:absolute;top:7px;color:var(--white);font-family:"Cabin",sans-serif;font-weight:700;font-size:9.5px;text-decoration:none;transform:translateX(-50%);white-space:nowrap}
.main-nav a.active{color:#b7a3dd}
.main-nav a.active::after{content:"";position:absolute;left:50%;bottom:-8px;margin-left:-4px;border:4px solid transparent;border-bottom-color:var(--white)}

/* hero */
.hero{left:8px;top:104px;width:679px;height:294px;background:radial-gradient(ellipse 110px 90px at 330px 150px,#e58a3a 0%,#a75a2a 35%,rgba(60,55,55,0) 100%),linear-gradient(135deg,#2a2a2e 0%,#55565c 45%,#8d8f96 70%,#3a3b40 100%)}
.appointment{left:467px;top:132px;width:181px;height:238px;background:#f4f4f4;border-radius:3px;box-shadow:0 1px 4px rgba(0,0,0,.35)}
.appointment-title{left:460px;top:146px;width:194px;height:26px;background:var(--purple-deep);color:var(--white);font-family:"Cabin",sans-serif;font-weight:700;font-size:11px;display:flex;align-items:center;justify-content:center}
.field{position:absolute;left:498px;width:140px;height:19px;background:var(--white);border:1px solid #d6d6d6;font-size:6.5px;font-weight:600;color:#333;padding:5px 0 0 9px}
.field-icon{position:absolute;left:477px;width:18px;height:19px;background:#e6e6e6;border:1px solid #d2d2d2;display:flex;align-items:center;justify-content:center}
.field.select::after{content:"";position:absolute;right:5px;top:7px;border:3px solid transparent;border-top:4px solid #555}
.field.select::before{content:"";position:absolute;right:18px;top:0;bottom:0;border-left:1px solid #d6d6d6}
.submit{left:499px;top:341px;width:107px;height:16px;background:#111;color:var(--white);font-size:7px;font-weight:700;display:flex;align-items:center;justify-content:center}

/* welcome */
.welcome{left:8px;top:398px;width:679px;height:298px;background:var(--welcome-bg)}
.welcome h1{position:absolute;left:0;top:32px;width:679px;text-align:center;font-family:"Cabin",sans-serif;font-weight:700;font-size:18px;color:var(--ink)}
.welcome h1 span{color:var(--purple-light)}
.divider{position:absolute;top:75px;height:1px;background:#cfd3d8;width:240px}
.divider-mark{position:absolute;left:336px;top:71px;width:8px;height:9px;border-radius:50%;background:var(--purple-deep)}
.welcome p{position:absolute;left:44px;width:600px;font-size:8.2px;line-height:1.45;color:var(--body)}
.welcome p b{color:var(--purple-deep);font-weight:600}
.cta{position:absolute;top:244px;width:150px;height:24px;background:var(--purple-deep);color:var(--white);font-family:"Cabin",sans-serif;font-weight:700;font-size:9.5px;display:flex;align-items:center;padding-left:40px;clip-path:polygon(0 0,93% 0,100% 50%,93% 100%,0 100%)}
.cta svg{position:absolute;left:10px;top:5px}

/* services */
.services{left:8px;top:696px;width:679px;height:306px;background:var(--white)}
.services h2{position:absolute;left:0;top:34px;width:679px;text-align:center;font-family:"Cabin",sans-serif;font-weight:700;font-size:14.5px;color:var(--ink)}
.service-map{left:0;top:696px}
.service-map text{font-family:"Open Sans",sans-serif;font-size:7.3px;font-weight:600;fill:#333}

/* footer */
.site-footer{left:8px;top:1002px;width:679px;height:171px;background:var(--footer)}
.footer-logo{left:56px;top:1070px;display:flex;align-items:center;gap:6px}
.footer-logo .logo-name{font-size:14px;color:#e58a3a}
.footer-logo .logo-dot{background:var(--purple)}
.footer-col{color:#d8d8d8;font-size:7.4px}
.footer-col h3{font-family:"Cabin",sans-serif;font-weight:700;font-size:9px;color:var(--white);padding-bottom:7px;border-bottom:1px solid #555;margin-bottom:8px}
.footer-col li{list-style:none;line-height:11.6px}
.footer-col .line{display:flex;gap:6px;line-height:11.5px;margin-bottom:11px}
.map{left:424px;top:1024px;width:214px;height:128px;background:linear-gradient(135deg,#e9e4d6,#d9dfe6 55%,#e8e1cf)}
.copyright{left:8px;top:1173px;width:679px;height:17px;background:var(--purple-deep);color:var(--white);font-size:5.8px;font-weight:700;display:flex;align-items:center;justify-content:space-between;padding:0 10px 0 18px}
.copyright .dots{display:flex;gap:3px}
.copyright .dots i{display:block;width:10px;height:10px;border-radius:50%;background:var(--white)}
</style>
</head>
<body>
<div class="page">

  <header class="site-header abs"></header>
  <div class="top-strip abs">
    <svg width="10" height="10" viewBox="0 0 10 10"><circle cx="5" cy="5" r="4.5" fill="none" stroke="#fff"/><rect x="2.5" y="3.3" width="5" height="3.4" fill="none" stroke="#fff" stroke-width=".8"/></svg>
    <span>info@brambleridgepodiatry.net</span>
    <span><i class="social-dot"></i> <i class="social-dot"></i></span>
  </div>
  <div class="logo-box abs"><span class="logo-dot"></span><span class="logo-name">Bramble Ridge<br>Podiatry</span></div>
  <div class="contact-row abs">
    <span><svg width="14" height="14" viewBox="0 0 14 14"><circle cx="7" cy="7" r="6.3" fill="none" stroke="#fff"/><path d="M4.6 3.8l1.3-.3.8 1.8-.8.7c.4.9 1.1 1.6 2 2l.7-.8 1.8.8-.3 1.3c-3 .2-5.7-2.5-5.5-5.5z" fill="#fff"/></svg>1300 482 907</span>
    <span><svg width="14" height="14" viewBox="0 0 14 14"><circle cx="7" cy="7" r="6.3" fill="none" stroke="#fff"/><path d="M7 3.3a2.3 2.3 0 0 1 2.3 2.3C9.3 7.4 7 10.5 7 10.5S4.7 7.4 4.7 5.6A2.3 2.3 0 0 1 7 3.3z" fill="#fff"/><circle cx="7" cy="5.6" r=".9" fill="#6b449b"/></svg>Suite 214 / 86 Alder Lane Ashford 3100</span>
  </div>

  <nav class="main-nav abs">
    <a class="active" href="#" style="left:271px">HOME</a>
    <a href="#" style="left:341px">ABOUT US</a>
    <a href="#" style="left:422px">SERVICES &#8964;</a>
    <a href="#" style="left:500px">CONTACT</a>
    <a href="#" style="left:566px">BLOG</a>
  </nav>

  <div class="hero abs" role="img" aria-label="Runner's foot on a treadmill with glowing heel bones highlighted"></div>

  <form class="appointment abs" aria-label="Schedule an Appointment"></form>
  <div class="appointment-title abs">Schedule an Appointment</div>
  <div class="field-icon" style="top:183px"><svg width="9" height="9" viewBox="0 0 9 9"><circle cx="4.5" cy="2.6" r="2" fill="#555"/><path d="M.8 9c0-2.4 1.6-3.8 3.7-3.8S8.2 6.6 8.2 9z" fill="#555"/></svg></div>
  <div class="field" style="top:183px">NAME</div>
  <div class="field-icon" style="top:207px"><svg width="9" height="9" viewBox="0 0 9 9"><path d="M1.4.6l1.7-.3 1 2.2-1 .9c.5 1.1 1.3 1.9 2.4 2.4l.9-1 2.2 1-.3 1.7C4.6 7.8 1.2 4.4 1.4.6z" fill="#555"/></svg></div>
  <div class="field" style="top:207px">MOBILE PHONE</div>
  <div class="field-icon" style="top:231px;font-size:9px;color:#555">@</div>
  <div class="field" style="top:231px">EMAIL</div>
  <div class="field-icon" style="top:255px"><svg width="7" height="9" viewBox="0 0 7 9"><rect x="1" y="0" width="5" height="9" rx="2" fill="#555"/></svg></div>
  <div class="field select" style="top:255px">INTERESTED IN</div>
  <div class="field-icon" style="top:280px"><svg width="10" height="8" viewBox="0 0 10 8"><rect x=".5" y=".5" width="9" height="7" fill="none" stroke="#555"/><path d="M.5.5L5 4.5 9.5.5" fill="none" stroke="#555"/></svg></div>
  <div class="field" style="top:279px;height:56px">MESSAGE</div>
  <div class="submit abs">SUBMIT</div>

  <section class="welcome abs">
    <h1>Welcome to <span>Bramble Ridge Podiatry</span></h1>
    <div class="divider" style="left:73px"></div>
    <div class="divider-mark"></div>
    <div class="divider" style="left:366px"></div>
    <p style="top:100px">Bramble Ridge Podiatry is a Podiatry clinic in the heart of Ashford CBD. We are located between Elm &amp; Harbour Streets in the Northgate Business Centre.</p>
    <p style="top:123px">Our podiatrists are fully qualified health professionals who are able to diagnose, treat, manage or help to prevent all medical conditions that affect the feet and lower limb.</p>
    <p style="top:156px">We provide General Podiatry Treatment and some Specialised Services in relation to various foot conditions, including Sports Injuries, Orthotic Therapy and Nail Surgery.</p>
    <p style="top:189px">For Appointments or Enquiries please call us on <b>1300 482 907</b> or email: <b>info@brambleridgepodiatry.net</b></p>
    <a class="cta" style="left:186px"><svg width="18" height="14" viewBox="0 0 18 14"><path d="M2 7l5 5L16 2" fill="none" stroke="#9fb3e6" stroke-width="3"/></svg>OUR SERVICES</a>
    <a class="cta" style="left:343px;padding-left:33px"><svg width="15" height="15" viewBox="0 0 15 15"><circle cx="7.5" cy="7.5" r="7" fill="#7d88cf"/><path d="M6 4.5l4.5 3-4.5 3z" fill="#fff"/></svg>TREATMENT VIDEOS</a>
  </section>

  <section class="services abs">
    <h2>Our Podiatry Treatment Services</h2>
  </section>
  <svg class="service-map abs" width="695" height="306" viewBox="0 696 695 306">
    <g stroke="#cfcfcf" stroke-width=".8">
      <line x1="267" y1="790" x2="330" y2="790"/><line x1="187" y1="814" x2="330" y2="814"/>
      <line x1="267" y1="838" x2="330" y2="838"/><line x1="187" y1="862" x2="340" y2="862"/>
      <line x1="267" y1="886" x2="345" y2="886"/><line x1="187" y1="910" x2="345" y2="910"/>
      <line x1="267" y1="934" x2="330" y2="934"/><line x1="187" y1="958" x2="330" y2="958"/>
      <line x1="370" y1="827" x2="427" y2="827"/><line x1="370" y1="851" x2="507" y2="851"/>
      <line x1="370" y1="875" x2="427" y2="875"/><line x1="360" y1="899" x2="507" y2="899"/>
      <line x1="355" y1="923" x2="427" y2="923"/>
    </g>
    <rect x="306" y="776" width="84" height="194" rx="38" fill="#4a2d8f" role="img" aria-label="Large purple foot silhouette illustration"/>
    <g fill="#fff" stroke="#4a2d8f" stroke-width="1.3">
      <circle cx="256" cy="790" r="11"/><circle cx="176" cy="814" r="11"/>
      <circle cx="256" cy="838" r="11"/><circle cx="176" cy="862" r="11"/>
      <circle cx="256" cy="886" r="11"/><circle cx="176" cy="910" r="11"/>
      <circle cx="256" cy="934" r="11"/><circle cx="176" cy="958" r="11"/>
      <circle cx="438" cy="827" r="11"/><circle cx="518" cy="851" r="11"/>
      <circle cx="438" cy="875" r="11"/><circle cx="518" cy="899" r="11"/>
      <circle cx="438" cy="923" r="11"/>
    </g>
    <text x="237" y="793" text-anchor="end">Nails</text>
    <text x="157" y="817" text-anchor="end">Corns</text>
    <text x="237" y="841" text-anchor="end">Callus</text>
    <text x="157" y="865" text-anchor="end">Warts</text>
    <text x="237" y="889" text-anchor="end">Skin Disorders</text>
    <text x="157" y="908" text-anchor="end">Heel Pain / Heel Spurs / Arch</text>
    <text x="157" y="918" text-anchor="end">Pain-Plantar Fasciitis,</text>
    <text x="237" y="932" text-anchor="end">Ankle Pain / Shin</text>
    <text x="237" y="942" text-anchor="end">Splints / Knee Pain</text>
    <text x="157" y="956" text-anchor="end">Bunions, Hammertoes and</text>
    <text x="157" y="966" text-anchor="end">Toe Deformities</text>
    <text x="458" y="830">Diabetic Management</text>
    <text x="538" y="854">Nail Surgery</text>
    <text x="458" y="878">Biomechanical Assessment</text>
    <text x="538" y="902">Gait Analysis</text>
    <text x="458" y="926">Orthotic Therapy</text>
  </svg>

  <footer class="site-footer abs"></footer>
  <div class="footer-logo abs"><span class="logo-dot"></span><span class="logo-name">Bramble Ridge<br>Podiatry</span></div>
  <div class="footer-col abs" style="left:182px;top:1024px;width:56px">
    <h3>QUICK LINKS</h3>
    <ul><li>Home</li><li>About Us</li><li>Services</li><li>Contact Us</li><li>Blog</li></ul>
  </div>
  <div class="footer-col abs" style="left:272px;top:1024px;width:121px">
    <h3>CONTACT</h3>
    <div class="line"><svg width="6" height="8" viewBox="0 0 6 8"><path d="M3 0a3 3 0 0 1 3 3c0 2-3 5-3 5S0 5 0 3a3 3 0 0 1 3-3z" fill="#6b449b"/></svg><span>Bramble Ridge Podiatry<br>Suite 214<br>86 Alder Lane<br>Ashford 3100</span></div>
    <div class="line"><svg width="8" height="8" viewBox="0 0 9 9"><path d="M1.4.6l1.7-.3 1 2.2-1 .9c.5 1.1 1.3 1.9 2.4 2.4l.9-1 2.2 1-.3 1.7C4.6 7.8 1.2 4.4 1.4.6z" fill="#6b449b"/></svg><span>1300 482 907</span></div>
    <div class="line"><svg width="8" height="7" viewBox="0 0 10 8"><rect x=".5" y=".5" width="9" height="7" fill="#6b449b"/><path d="M.5.5L5 4.5 9.5.5" fill="none" stroke="#1d1d1d"/></svg><span>info@brambleridgepodiatry.net</span></div>
  </div>
  <div class="map abs" role="img" aria-label="Street map of the clinic location with a red marker"></div>

  <div class="copyright abs"><span>COPYRIGHT © 2016 BRAMBLE RIDGE PODIATRY. ALL RIGHTS RESERVED.</span><span class="dots"><i></i><i></i></span></div>
</div>
</body>
</html>
```